Trade Show Design

Two, doublesided backdrops/one doublesided banner/one countertop. I have 3 sample pictures of the 3 items that we are purchasing and all the dimensions are listed on the file names.
website: www.brickwisestudio.net
We are a training center that teaches homeowner's how to do their own home renovations through in-person classes with hands-on training.
We are looking to update our tradeshow displays utilizing stock photos as our photos do not have high enough resolution. I have attached lots of example pictures to select from but some of my favourites that I want to use are over 10 MB so they won't upload. Will have to figure out a different way to upload. Our tagline is tackle any project like a pro. We also use words such as "learn to reno" or "practical, hands-on training". We want to use our current branding (pictures of our minivan are uploaded as well) and our color palette document and really show people what we are all about - classes that people can attend so they can learn to reno their home.
Updates

For the 2 backdrops, we would like them to either be stand-alone or together incase we go to a trade show and only have room for 1 of them. They are to be different designs, front and back but a continuous flow if we are to use them together. Again, I have to figure out how to upload additional pictures as some of the ones I want to use are larger. Thanks!

Same with the Banner that is also double-sided - this is to be a different design for the back and front. We want minimal wording on everything but we really want to showcase what we do so that people can figure it out quickly when they walk by our booth....we offer in-person class with hands-on training. Learn to do by doing. Like on our vehicle that I sent example pictures of, we can put a list of a few topics so that people can understand:
Renovation Topics:
Bathroom
Drywall
Flooring
Tiling
Basement
Framing
Plumbing
Baseboards
Feature Walls

Here is the link to the Vornel Box to additional photos.

https://files.vornelbox.net/shared/7QK4r_mz2-TX8LwBnPe5YuJsdA0fGhRkZ?view=open

Thanks,
Marla

```html
<!DOCTYPE html>
<html lang="en">
<head>
<meta charset="utf-8">
<title>Brickwise Studio – Trade Show Backdrops</title>
<link rel="stylesheet" href="https://fonts.googleapis.com/css2?family=Anton&family=Baloo+2:wght@700&family=Poppins:wght@400;500&display=swap">
<style>
  :root {
    --bg: #d9e1e8;
    --teal: #2a6c79;
    --orange: #e0a43d;
    --cream: #e8e7b6;
    --sky: #b6d3ef;
    --white: #ffffff;
    --ink: #1f5a66;
  }
  * { box-sizing: border-box; margin: 0; padding: 0; }
  html, body { width: 1200px; height: 731px; overflow: hidden; background: var(--bg); }
  body { position: relative; font-family: "Poppins", sans-serif; }

  .backdrop {
    position: absolute; top: 132px; width: 560px; height: 467px;
    overflow: hidden; background: var(--cream);
    box-shadow: 0 6px 18px rgba(40, 60, 80, .18);
  }
  .backdrop--front { left: 25px; }
  .backdrop--back { left: 615px; }

  .tile { position: absolute; display: flex; flex-direction: column; align-items: center; justify-content: center; text-align: center; padding: 0 8px; }
  .tile--cream { background: var(--cream); }
  .tile--teal { background: var(--teal); }
  .tile--orange { background: var(--orange); }
  .tile--sky { background: var(--sky); }

  .photo { position: absolute; }
  .photo--warm { background: linear-gradient(135deg, #b89a78, #6f5b4c); }
  .photo--studio { background: linear-gradient(135deg, #d8d3cc, #7a8aa0); }
  .photo--room { background: linear-gradient(135deg, #e6e2dc, #a78f74); }
  .photo--shop { background: linear-gradient(135deg, #8a7f76, #c9b9a6); }
  .photo--ceiling { background: linear-gradient(160deg, #f1f0ee, #c99a8c); }
  .photo--pair { background: linear-gradient(135deg, #e4e2df, #9aa8b7); }
  .photo--olive { background: linear-gradient(160deg, #d7d6a2, #a9a878); }

  .topics {
    font-family: "Baloo 2", sans-serif; font-weight: 700; text-transform: uppercase;
    font-size: 11.5px; line-height: 1.4; letter-spacing: .01em;
  }
  .topics--white { color: var(--white); }
  .topics--teal { color: var(--teal); }
  .icon { width: 36px; height: 36px; margin-bottom: 10px; }

  .brand { display: flex; flex-direction: column; align-items: center; gap: 4px; max-width: 100%; }
  .brand__name {
    display: flex; align-items: center; gap: 5px; white-space: nowrap;
    font-family: "Baloo 2", sans-serif; font-weight: 700; font-size: 14px; color: var(--orange);
  }
  .brand__mark { width: 10px; height: 10px; background: var(--orange); flex: none; }
  .brand__tagline { font-size: 7.5px; color: var(--teal); white-space: nowrap; }

  .headline {
    font-family: "Anton", sans-serif; color: var(--white); line-height: 1.02;
    font-size: 50px; letter-spacing: -.01em;
  }
  .swash { width: 110px; height: 16px; margin-top: 4px; }

  .url {
    display: flex; align-items: center; height: 24px; padding-right: 10px;
    background: var(--teal); border-radius: 4px; color: var(--white);
    font-size: 8.5px; font-weight: 500; white-space: nowrap;
  }
  .url__dot {
    width: 24px; height: 24px; border-radius: 50%; background: #f2b81d;
    display: flex; align-items: center; justify-content: center; margin-right: 6px; flex: none;
  }

  .back-column {
    position: absolute; left: 0; top: 0; width: 40%; height: 100%;
    display: flex; flex-direction: column; align-items: center; padding: 45px 8px 30px;
  }
  .back-column .brand { margin-bottom: 52px; }
  .back-headline { font-family: "Anton", sans-serif; font-size: 38px; line-height: 1.05; text-align: center; color: var(--ink); }
  .back-headline__tag {
    display: inline-block; background: var(--orange); color: var(--white);
    padding: 0 8px; border-radius: 3px; transform: rotate(-3deg); margin: 2px 0;
  }
  .back-column .swash { margin-bottom: auto; }
</style>
</head>
<body>

<section class="backdrop backdrop--front" aria-label="Front backdrop: Learn To Reno">
  <div class="photo photo--warm" style="left:0;top:0;width:25.8%;height:34.6%" role="img" aria-label="Photo of a woman measuring a wooden board in a workshop"></div>
  <div class="tile tile--cream" style="left:25.8%;top:0;width:26.1%;height:34.6%">
    <div class="brand">
      <span class="brand__name"><span class="brand__mark"></span>Brickwise Studio</span>
      <span class="brand__tagline">Build it right, build it yourself.</span>
    </div>
  </div>
  <div class="photo photo--studio" style="left:51.9%;top:0;width:26%;height:34.6%" role="img" aria-label="Photo of a smiling woman holding a hammer"></div>
  <div class="tile tile--orange" style="left:77.9%;top:0;width:22.1%;height:34.6%">
    <svg class="icon" viewBox="0 0 40 40" aria-hidden="true"><rect x="6" y="8" width="22" height="10" rx="2" fill="#fff"/><rect x="28" y="11" width="8" height="3" fill="#fff"/><rect x="11" y="18" width="9" height="12" fill="#fff"/><rect x="9" y="30" width="13" height="5" rx="1" fill="#fff"/></svg>
    <div class="topics topics--white">Drywall<br>Feature Walls<br>Framing</div>
  </div>

  <div class="tile tile--cream" style="left:0;top:34.6%;width:25.8%;height:34.8%">
    <svg class="icon" viewBox="0 0 40 40" aria-hidden="true"><rect x="6" y="20" width="26" height="5" rx="2" transform="rotate(-45 19 22)" fill="#2a6c79"/><path d="M22 6 L34 10 L30 18 L20 12 Z" fill="#2a6c79"/></svg>
    <div class="topics topics--teal">Tiling<br>Bathroom<br>Plumbing</div>
  </div>
  <div class="tile tile--teal" style="left:25.8%;top:34.6%;width:52.1%;height:34.8%">
    <div class="headline">Learn<br>To Reno</div>
    <svg class="swash" viewBox="0 0 110 16" aria-hidden="true"><path d="M2 8 Q55 6 108 3 M40 14 Q70 6 106 6" stroke="#e0a43d" stroke-width="1.6" fill="none" stroke-linecap="round"/></svg>
  </div>
  <div class="tile tile--sky" style="left:77.9%;top:34.6%;width:22.1%;height:34.8%">
    <svg class="icon" viewBox="0 0 40 40" aria-hidden="true"><rect x="6" y="18" width="28" height="16" rx="2" fill="#2a6c79"/><rect x="12" y="6" width="4" height="14" fill="#2a6c79"/><rect x="24" y="6" width="4" height="14" fill="#2a6c79"/></svg>
    <div class="topics topics--teal">Flooring<br>Baseboards<br>Basement</div>
  </div>

  <div class="photo photo--room" style="left:0;top:69.4%;width:35%;height:30.6%" role="img" aria-label="Photo of a couple with paint roller and tool belt in a room under renovation"></div>
  <div class="tile tile--cream" style="left:35%;top:69.4%;width:30.9%;height:30.6%">
    <div class="url"><span class="url__dot"><svg width="9" height="11" viewBox="0 0 9 11" aria-hidden="true"><path d="M1 0 L8 6 L4.5 6.5 L6 10 L4.5 10.6 L3 7 L1 9 Z" fill="#2a6c79"/></svg></span>brickwisestudio.net</div>
  </div>
  <div class="photo photo--shop" style="left:65.9%;top:69.4%;width:34.1%;height:30.6%" role="img" aria-label="Photo of a woman in safety glasses using a power drill"></div>
</section>

<section class="backdrop backdrop--back" aria-label="Back backdrop: Practical, Hands-on Training">
  <div class="photo photo--olive" style="left:0;top:0;width:40%;height:100%" role="img" aria-label="Olive-tinted photo of a person sanding wood"></div>
  <div class="back-column">
    <div class="brand">
      <span class="brand__name"><span class="brand__mark"></span>Brickwise Studio</span>
      <span class="brand__tagline">Build it right, build it yourself.</span>
    </div>
    <div class="back-headline">Practical,<br><span class="back-headline__tag">Hands-on</span><br>Training.</div>
    <svg class="swash" viewBox="0 0 110 16" aria-hidden="true"><path d="M4 10 Q55 8 106 6" stroke="#e0a43d" stroke-width="1.6" fill="none" stroke-linecap="round"/></svg>
    <div class="url"><span class="url__dot"><svg width="9" height="11" viewBox="0 0 9 11" aria-hidden="true"><path d="M1 0 L8 6 L4.5 6.5 L6 10 L4.5 10.6 L3 7 L1 9 Z" fill="#2a6c79"/></svg></span>brickwisestudio.net</div>
  </div>

  <div class="tile tile--teal" style="left:40%;top:0;width:31.6%;height:33.5%">
    <svg class="icon" viewBox="0 0 40 40" aria-hidden="true"><rect x="6" y="8" width="22" height="10" rx="2" fill="#fff"/><rect x="28" y="11" width="8" height="3" fill="#fff"/><rect x="11" y="18" width="9" height="12" fill="#fff"/><rect x="9" y="30" width="13" height="5" rx="1" fill="#fff"/></svg>
    <div class="topics topics--white">Drywall<br>Feature Walls<br>Framing</div>
  </div>
  <div class="tile tile--cream" style="left:71.6%;top:0;width:28.4%;height:33.5%">
    <svg class="icon" viewBox="0 0 40 40" aria-hidden="true"><rect x="6" y="18" width="28" height="16" rx="2" fill="#2a6c79"/><rect x="12" y="6" width="4" height="14" fill="#2a6c79"/><rect x="24" y="6" width="4" height="14" fill="#2a6c79"/></svg>
    <div class="topics topics--teal">Flooring<br>Baseboards<br>Basement</div>
  </div>
  <div class="photo photo--ceiling" style="left:40%;top:33.5%;width:60%;height:33%" role="img" aria-label="Photo of a couple installing a ceiling light fixture"></div>
  <div class="photo photo--pair" style="left:40%;top:66.5%;width:31.6%;height:33.5%" role="img" aria-label="Photo of a smiling couple holding a drill and tools"></div>
  <div class="tile tile--sky" style="left:71.6%;top:66.5%;width:28.4%;height:33.5%">
    <svg class="icon" viewBox="0 0 40 40" aria-hidden="true"><rect x="6" y="20" width="26" height="5" rx="2" transform="rotate(-45 19 22)" fill="#2a6c79"/><path d="M22 6 L34 10 L30 18 L20 12 Z" fill="#2a6c79"/></svg>
    <div class="topics topics--teal">Tiling<br>Bathroom<br>Plumbing</div>
  </div>
</section>

</body>
</html>
```